Maple Lantern Productions web site

I need to build a website for a new company I am launching next month. Maple Lantern Productions is a company based in New England that provides sound, lighting, and audio visual services to weddings, corporate, and any other cusomer base looking for quality service for a fair price. Looking for somebody to do a full site not just the image files. I am looking to keep the colors of my logo (orange and black) and possibly grey and white. I am looking to build my site very similar to brightvaleevents.example, which is owned by a friend of mine. I like how he has the big pictures that load in to the site and the basic menu items. I'll need a gallery of photos. The designs should communicate quality, value and trust.
My website address is maplelanternco.example.
Updates

Hi and thanks to everyone for posting such great ideas for our new design.I have some items that I'd like to ask you all to focus on in your revisions.I like how http://www.brightvaleevents.example/ website has five or six high res pictures that change in a slideshow format with a caption that loads in for each one for the different types of services. Try and capture pics like these and with teh same headings as he has. The basic menu designs have been interesting.I am more fond of the menus that are more white with some orange as I dont want it to be too dark. I'm curious to see how your galleries will work and if i'll be able to edit the pages myself? I have some more info on the company for you to fill in:website address is ciderhouseco.comemail: info@ciderhouseco.comaddress: Maple Lantern Productions57 Littlefield StreetAvon, MA 02417"New England's finest DJ's, lighting and sound, video and more. Creating memories one perfect event at a time."Put this under the loading pictures as a tagline.About Cider HouseCider House Productions is a collection of New England's finest talent, ready to make your next event the one you've dreamed of. We have the skills and expertise to deliver your vision of your perfect event. From elegant weddings to themed mitzvah's, corporate av, videography and detail lighting, we offer all of the elements to make your event a success. Added Wednesday, March 1, 2017

Designer's Please also make sure that your design flows well on any device it is being viewed on as well. Thanks. Added Wednesday, March 1, 2017

Project Deadline Extended Reason: Hello designerThank you all very much for your hard work on our project. Im sorry but i need to extend the date of my project. Our parent conpany Rook Nine Prodactions sponsors Bay Youth Assemblies and we are currently at their leadership conference on the Cape. I will be back in on Monday and with your help will get this finished by Thursday the 16th. Thanks Added Thursday, March 9, 2017

Project Deadline Extended Reason: One of the designers is not responding so I now have to make revisions with other designers. I hope to get this website done over the weekends so please get your revisions as soon as possible. Thank you. I am also upgrading the budget another $75 to hopefully get some more interest on my project. Added Wednesday, March 15, 2017

Target Market(s)

Wedding - Corporate -

Industry/Entity Type

It Company

Coding

Coded - Design and coding required

Number of Pages Required

5+ page

Font styles to use
Sans Serif

Requirements
Must have
• Photo Gallery - I want to be able to edit it myself
Nice to have
• I like the look of my friends website brightvaleevents.example

```html
<!DOCTYPE html>
<html lang="en">
<head>
<meta charset="utf-8">
<title>Maple Lantern Productions</title>
<link rel="stylesheet" href="https://fonts.googleapis.com/css2?family=Montserrat:wght@400;600;700&family=Open+Sans:wght@400;600&display=swap">
<style>
:root{
  --orange:#f26522;
  --orange-dark:#d9531a;
  --ink:#2b2b2b;
  --text:#555;
  --muted:#777;
  --white:#fff;
  --footer:#1f1f1f;
  --field:#3a3a3a;
  --line:#d6d6d6;
}
*{box-sizing:border-box;margin:0;padding:0}
html,body{width:1200px;height:4945px;overflow:hidden}
body{position:relative;background:var(--white);font-family:"Open Sans",Arial,sans-serif;color:var(--text)}
.abs{position:absolute}
h1,h2,h3,.band-title,.brand,.nav a{font-family:"Montserrat",Arial,sans-serif}

/* header */
.site-header{left:0;top:0;width:1200px;height:110px;background:var(--white)}
.brand{left:100px;top:16px;display:flex;align-items:center;gap:14px;color:var(--ink);font-weight:700;line-height:1.05}
.brand-mark{width:76px;height:76px;border-radius:50%;background:var(--orange)}
.brand-name{font-size:26px;letter-spacing:1px}
.brand-sub{font-size:14px;letter-spacing:6px}
.top-contact{right:100px;top:24px;display:flex;gap:30px;font-size:12px;color:var(--muted)}
.top-contact span{display:flex;align-items:center;gap:8px}
.nav{right:95px;top:64px;display:flex;gap:40px}
.nav a{font-size:14px;color:#444;text-decoration:none}

/* hero */
.hero{left:0;top:110px;width:1200px;height:600px;clip-path:polygon(0 0,100% 0,100% 86%,50% 100%,0 86%);
  background:linear-gradient(100deg,#4f4a3c 0%,#8e8069 35%,#c9b79a 55%,#6d6656 80%,#3d3a31 100%)}
.hero-shade{inset:0;background:rgba(20,18,14,.35)}
.hero-title{left:0;top:168px;width:1200px;text-align:center;color:var(--white);font-size:58px;font-weight:700;letter-spacing:1px}
.hero-sub{left:0;top:258px;width:1200px;text-align:center;color:var(--white);font-family:"Open Sans",sans-serif;font-size:36px;font-weight:400}
.hero-btn{left:427px;top:344px;width:346px;height:46px;border:2px solid var(--white);color:var(--white);font-size:24px;display:flex;align-items:center;justify-content:center}
.hero-dots{left:570px;top:525px;display:flex;gap:10px}
.hero-dots i{width:11px;height:11px;border-radius:50%;border:2px solid var(--white)}
.hero-dots i:first-child{background:var(--white)}

/* welcome */
.welcome-title{left:0;top:770px;width:1200px;text-align:center;font-size:30px;font-weight:600;color:var(--ink)}
.welcome-text{left:175px;top:835px;width:850px;font-size:13px;line-height:23px;text-align:center}
.btn-solid{background:var(--orange);color:var(--white);font-size:17px;display:flex;align-items:center;justify-content:center}
.welcome-btn{left:535px;top:955px;width:130px;height:38px}

/* bands */
.band{left:0;width:1200px;height:55px;background:var(--orange)}
.band::before{content:"";position:absolute;left:470px;top:-12px;width:260px;height:14px;background:var(--orange);clip-path:polygon(8% 0,92% 0,100% 100%,0 100%)}
.band-title{position:absolute;inset:0;display:flex;align-items:center;justify-content:center;color:var(--white);font-size:21px;font-weight:700;letter-spacing:.5px}

/* services */
.photo{overflow:hidden}
.service-title{font-size:28px;font-weight:600;color:var(--ink)}
.service-title em{font-style:normal;color:var(--orange)}
.service-text{font-size:12.5px;line-height:22px;width:390px}
.btn-outline{border:2px solid var(--orange);color:var(--orange);font-size:14px;width:110px;height:32px;display:flex;align-items:center;justify-content:center}

/* about */
.about{left:0;top:2535px;width:1200px;height:385px;background:linear-gradient(90deg,#1c1424 0%,#3a2146 45%,#2d1c3c 70%,#16111d 100%)}
.about-shade{inset:0;background:rgba(10,8,14,.35)}
.about-title{left:0;top:2600px;width:1200px;text-align:center;color:var(--white);font-size:30px;font-weight:600}
.about-text{left:195px;width:810px;text-align:center;color:#e9e6ee;font-size:13px;line-height:23px}

/* testimonials */
.quote{width:445px;height:150px;border:1px solid var(--line);box-shadow:0 2px 8px rgba(0,0,0,.08);padding:28px 36px;font-size:12.5px;line-height:22px;text-align:center;color:var(--muted)}
.client{display:flex;align-items:center;gap:14px;font-size:13px;font-weight:600;color:var(--ink)}
.avatar{width:60px;height:60px;border-radius:50%;background:radial-gradient(circle at 50% 40%,#b98a6a,#5a3a2a)}

/* footer */
.site-footer{left:0;top:4355px;width:1200px;height:590px;background:var(--footer);color:var(--white)}
.contact-title{left:0;top:4398px;width:1200px;text-align:center;font-size:34px;font-weight:400;letter-spacing:1px;color:var(--white)}
.contact-sub{left:0;top:4455px;width:1200px;text-align:center;font-size:14px;color:#ddd}
.footer-brand{left:170px;top:4490px;text-align:center;color:var(--white);font-family:"Montserrat",sans-serif;font-weight:700;line-height:1.1}
.footer-brand .brand-mark{width:96px;height:96px;background:var(--white);margin:0 auto 14px}
.footer-brand .brand-name{font-size:30px;letter-spacing:1px}
.footer-brand .brand-sub{font-size:16px;letter-spacing:8px}
.footer-info{left:192px;display:flex;align-items:center;gap:18px;font-size:14px;color:#eee}
.field{left:568px;width:400px;background:var(--field);color:#ccc;font-size:14px;padding:0 18px;display:flex;align-items:center}
.field.message{align-items:flex-start;padding-top:14px}
.submit{left:568px;top:4810px;width:130px;height:42px;font-size:17px;letter-spacing:1px}
.footer-rule{left:100px;top:4872px;width:1000px;height:1px;background:#444}
.copyright{left:0;top:4890px;width:1200px;text-align:center;font-size:11px;color:#aaa}
</style>
</head>
<body>

<header class="site-header abs">
  <div class="brand abs">
    <span class="brand-mark"></span>
    <span><span class="brand-name">MAPLE LANTERN</span><br><span class="brand-sub">PRODUCTIONS</span></span>
  </div>
  <div class="top-contact abs">
    <span><svg width="14" height="14" viewBox="0 0 24 24"><path fill="#f26522" d="M6.6 10.8a15 15 0 0 0 6.6 6.6l2.2-2.2c.3-.3.7-.4 1-.2 1.1.4 2.3.6 3.6.6.6 0 1 .4 1 1V20c0 .6-.4 1-1 1A17 17 0 0 1 3 4c0-.6.4-1 1-1h3.5c.6 0 1 .4 1 1 0 1.3.2 2.5.6 3.6.1.3 0 .7-.2 1z"/></svg>555 0142 7788</span>
    <span><svg width="15" height="12" viewBox="0 0 24 18"><rect x="1" y="1" width="22" height="16" fill="none" stroke="#f26522" stroke-width="2"/><path d="M1 1l11 9 11-9" fill="none" stroke="#f26522" stroke-width="2"/></svg>info@maplelantern.example</span>
  </div>
  <nav class="nav abs">
    <a href="#">Home</a><a href="#">Services</a><a href="#">About Us</a><a href="#">Testimonials</a><a href="#">Gallery</a><a href="#">Contact Us</a>
  </nav>
</header>

<section class="hero abs" role="img" aria-label="Photo of wedding guests celebrating at an evening reception">
  <div class="hero-shade abs"></div>
</section>
<h1 class="hero-title abs" style="top:278px">YOUR VISION OUR INNOVATION</h1>
<p class="hero-sub abs" style="top:368px">Innovative Concepts, Creative Design, Flawless Execution</p>
<div class="hero-btn abs" style="top:454px">Click Here For More Info</div>
<div class="hero-dots abs" style="top:635px"><i></i><i></i><i></i></div>

<h2 class="welcome-title abs">Welcome To Maple Lantern</h2>
<p class="welcome-text abs">Maple Lantern brings seasoned DJs, stage lighting, sound and video crews to weddings, galas and corporate nights across New England. We plan each detail with you, arrive early, test every cable and stay until the last song fades, so your guests remember the night while you simply enjoy it. From a quiet ceremony to a packed dance floor, our team shapes the room around your vision with care and honest pricing.</p>
<div class="welcome-btn btn-solid abs">Read More</div>

<div class="band abs" style="top:1070px"><span class="band-title">OUR SERVICES</span></div>

<!-- sound -->
<div class="photo abs" role="img" aria-label="Photo of a sound mixing console in a studio" style="left:100px;top:1220px;width:575px;height:232px;clip-path:polygon(0 0,86% 0,100% 100%,0 100%);background:linear-gradient(120deg,#0f1a24 0%,#24384a 40%,#6b4a2e 70%,#1a140e 100%)"></div>
<h3 class="service-title abs" style="left:710px;top:1250px"><em>Sound</em> Services</h3>
<p class="service-text abs" style="left:710px;top:1305px">Our sound crew sets up clear, balanced audio for every space, from garden vows to ballroom receptions. We bring tuned speakers, wireless microphones and a skilled engineer who watches levels all night, so every toast is heard and every song fills the room without ever drowning out conversation at the tables.</p>
<div class="btn-outline abs" style="left:710px;top:1465px">Read More</div>

<!-- lighting -->
<h3 class="service-title abs" style="left:100px;top:1678px"><em>Lighting</em> Services</h3>
<p class="service-text abs" style="left:100px;top:1732px">Lighting turns an ordinary hall into a space your guests will talk about for years. We design uplighting, pin spots, dance floor effects and custom monograms in your colours, then program each scene to follow the flow of the evening from dinner glow to late night party energy.</p>
<div class="btn-outline abs" style="left:100px;top:1890px">Read More</div>
<div class="photo abs" role="img" aria-label="Photo of blue stage lights beaming over a crowd" style="left:520px;top:1640px;width:585px;height:322px;clip-path:polygon(14% 0,100% 0,100% 100%,0 100%,0 30%);background:radial-gradient(ellipse at 50% 35%,#9fe6ff 0%,#2a7fb8 25%,#0b2a4a 60%,#050b18 100%)"></div>

<!-- audio -->
<div class="photo abs" role="img" aria-label="Photo of audio mixer faders close up" style="left:100px;top:2060px;width:575px;height:322px;clip-path:polygon(0 0,88% 0,100% 50%,82% 100%,0 100%);background:linear-gradient(110deg,#3a342e 0%,#8a7d6e 40%,#c9bfb2 60%,#4c443c 100%)"></div>
<h3 class="service-title abs" style="left:710px;top:2092px"><em>Audio</em> Services</h3>
<p class="service-text abs" style="left:710px;top:2148px">Our audio visual team handles projectors, screens, live video and presenter support for corporate meetings and celebrations alike. We test every input before doors open, keep spare gear on hand and stay beside the stage, so slides, speeches and videos run on time without a single missed cue.</p>
<div class="btn-outline abs" style="left:710px;top:2308px">Read More</div>

<div class="band abs" style="top:2480px"><span class="band-title">ABOUT US</span></div>

<section class="about abs" role="img" aria-label="Photo of a concert crowd under purple stage light">
  <div class="about-shade abs"></div>
</section>
<h2 class="about-title abs">Why We Are Special From Others</h2>
<p class="about-text abs" style="top:2665px">Maple Lantern Productions is a collection of the Northeast's finest talent, ready to make your next event the one you have dreamed of. We have the skills and the experience to deliver your vision, and we treat every booking with the same attention whether it is a small party or a grand wedding for three hundred guests.</p>
<p class="about-text abs" style="top:2790px">From elegant weddings to themed mitzvahs, corporate AV, videography and detail lighting, we offer every element your event needs to succeed. One team, one plan and one point of contact means fewer surprises, fair pricing and a night that runs smoothly from the first guest arriving to the final dance of the evening.</p>

<div class="band abs" style="top:2920px"><span class="band-title">Our Gallery</span></div>

<div class="photo abs" role="img" aria-label="Photo of DJ headphones on turntables in purple light" style="left:100px;top:3045px;width:390px;height:485px;background:linear-gradient(160deg,#1b1a5a 0%,#5b2fa0 40%,#c2307f 70%,#2a0f3a 100%)"></div>
<div class="photo abs" role="img" aria-label="Photo of an outdoor reception table at sunset" style="left:520px;top:3045px;width:585px;height:230px;background:linear-gradient(180deg,#c98a5a 0%,#e3b07a 35%,#8a5a3e 70%,#3e2a20 100%)"></div>
<div class="photo abs" role="img" aria-label="Photo of string lights over an evening party" style="left:520px;top:3305px;width:585px;height:225px;background:radial-gradient(ellipse at 50% 40%,#d79a5a 0%,#7a4a2e 40%,#2a1a14 100%)"></div>
<div class="photo abs" role="img" aria-label="Photo of a concert crowd in red stage light" style="left:100px;top:3580px;width:488px;height:280px;background:linear-gradient(180deg,#e04a3a 0%,#a2201e 45%,#3a0a10 100%)"></div>
<div class="photo abs" role="img" aria-label="Photo of warm blurred party lights" style="left:617px;top:3580px;width:488px;height:280px;background:radial-gradient(ellipse at 40% 45%,#c88a52 0%,#6e3e24 45%,#1e120c 100%)"></div>

<div class="band abs" style="top:3920px"><span class="band-title">Testimonials</span></div>

<p class="quote abs" style="left:142px;top:4030px">"The lighting was stunning and the DJ read our crowd perfectly. Every guest asked who did our music, and the whole team was kind, calm and right on time."</p>
<p class="quote abs" style="left:618px;top:4030px">"Our conference ran without a single glitch. Slides, microphones and video all worked, and the crew solved every request quickly and with a smile all day long."</p>
<div class="client abs" style="left:215px;top:4225px"><span class="avatar" role="img" aria-label="Client portrait"></span>- Sarah and Tom, Wedding Couple</div>
<div class="client abs" style="left:680px;top:4225px"><span class="avatar" role="img" aria-label="Client portrait"></span>- Event Manager, Local Firm</div>

<footer class="site-footer abs"></footer>
<h2 class="contact-title abs">GET IN TOUCH!</h2>
<p class="contact-sub abs">Use the contact form to ask us any questions</p>
<div class="footer-brand abs">
  <span class="brand-mark" style="display:block"></span>
  <span class="brand-name">MAPLE LANTERN</span><br><span class="brand-sub">PRODUCTIONS</span>
</div>
<div class="footer-info abs" style="top:4680px"><svg width="14" height="18" viewBox="0 0 24 32"><path fill="#fff" d="M12 0a11 11 0 0 0-11 11c0 8 11 21 11 21s11-13 11-21A11 11 0 0 0 12 0zm0 15a4 4 0 1 1 0-8 4 4 0 0 1 0 8z"/></svg>Maple Lantern, Productions England</div>
<div class="footer-info abs" style="top:4720px"><svg width="16" height="16" viewBox="0 0 24 24"><path fill="#fff" d="M6.6 10.8a15 15 0 0 0 6.6 6.6l2.2-2.2c.3-.3.7-.4 1-.2 1.1.4 2.3.6 3.6.6.6 0 1 .4 1 1V20c0 .6-.4 1-1 1A17 17 0 0 1 3 4c0-.6.4-1 1-1h3.5c.6 0 1 .4 1 1 0 1.3.2 2.5.6 3.6.1.3 0 .7-.2 1z"/></svg>+28 5550 1934</div>
<div class="footer-info abs" style="top:4760px"><svg width="16" height="12" viewBox="0 0 24 18"><path fill="#fff" d="M0 0h24v18H0z"/><path d="M1 1l11 9 11-9" fill="none" stroke="#1f1f1f" stroke-width="2"/></svg>info@maplelantern.example</div>

<div class="field abs" style="top:4515px;height:52px">Name</div>
<div class="field abs" style="top:4595px;height:52px">Email</div>
<div class="field message abs" style="top:4668px;height:124px">Message</div>
<div class="submit btn-solid abs">SUBMIT</div>
<div class="footer-rule abs"></div>
<p class="copyright abs">Copyright 2017 © Maple Lantern Productions. All Rights Reserved</p>

</body>
</html>
```